Modern Business Card

Modern professional business card with more than just logo and demographic info. Something memorable.

We are a trendy/modern chiropractic group with an emphasis on neurology, hence the minimalist-type brain logo. We want to convey that modern and technical aspect with professionalism and the elite nature of our practice environment.

```html
<!DOCTYPE html>
<html lang="en">
<head>
<meta charset="utf-8">
<title>Keystone Chiropractic – Business Card</title>
<link href="https://fonts.googleapis.com/css2?family=Cinzel:wght@400;600&family=Montserrat:wght@400;500&display=swap" rel="stylesheet">
<style>
  :root {
    --backdrop: #9a9a9a;
    --card-black: #1d1d1e;
    --brand-blue: #4a80c4;
    --paper-white: #ffffff;
    --text-light: #f2f2f2;
  }
  * { margin: 0; padding: 0; box-sizing: border-box; }
  html, body { width: 1200px; height: 930px; overflow: hidden; }
  body {
    background: radial-gradient(ellipse at 50% 40%, #b3b3b3 0%, var(--backdrop) 75%);
    position: relative;
    font-family: "Montserrat", sans-serif;
  }
  .card {
    position: absolute;
    width: 560px;
    height: 320px;
    border-radius: 22px;
    background: var(--card-black);
    overflow: hidden;
    box-shadow: 0 14px 30px rgba(0,0,0,0.35);
  }
  .card--front { left: 90px; top: 80px; }
  .card--back { left: 550px; top: 520px; }

  /* Front */
  .brand {
    position: absolute;
    inset: 0;
    display: flex;
    align-items: center;
    justify-content: center;
    gap: 18px;
  }
  .brand__dot {
    width: 56px; height: 56px;
    border-radius: 50%;
    background: var(--brand-blue);
  }
  .brand__name {
    font-family: "Cinzel", serif;
    font-weight: 400;
    color: var(--text-light);
    line-height: 1;
  }
  .brand__name .line-main { display: block; font-size: 44px; letter-spacing: 1px; }
  .brand__name .line-sub { display: block; font-size: 22px; letter-spacing: 2px; margin-top: 6px; }

  /* Back */
  .address {
    position: absolute;
    left: 38px; top: 78px;
    color: var(--text-light);
    font-size: 14px;
    line-height: 1.45;
  }
  .title-band {
    position: absolute;
    left: 0; top: 150px;
    width: 420px; height: 58px;
    background: var(--brand-blue);
    padding: 8px 0 0 40px;
    color: var(--paper-white);
  }
  .title-band__name {
    font-family: "Cinzel", serif;
    font-weight: 600;
    font-size: 21px;
    letter-spacing: 0.5px;
    line-height: 1.1;
  }
  .title-band__role { font-size: 13px; margin-top: 2px; }
  .emblem {
    position: absolute;
    left: 290px; top: -70px;
    width: 330px; height: 330px;
    border-radius: 50%;
    background: var(--paper-white);
    border: 8px solid var(--brand-blue);
  }
  .emblem-name {
    position: absolute;
    left: 310px; top: 92px;
    width: 230px;
    font-family: "Cinzel", serif;
    font-weight: 400;
    font-size: 24px;
    color: var(--brand-blue);
    text-align: center;
    line-height: 1.2;
  }
  .contact-list {
    position: absolute;
    left: 38px; bottom: 26px;
    list-style: none;
    color: var(--text-light);
    font-size: 14px;
    line-height: 1.6;
  }
  .contact-list li { display: flex; align-items: center; gap: 10px; }
  .contact-list svg { width: 13px; height: 13px; fill: var(--brand-blue); flex: none; }
  .contact-list .accent { color: var(--brand-blue); }
</style>
</head>
<body>

<section class="card card--front" aria-label="Card front">
  <div class="brand">
    <span class="brand__dot"></span>
    <p class="brand__name"><span class="line-main">KEYSTONE</span><span class="line-sub">CHIROPRACTIC</span></p>
  </div>
</section>

<section class="card card--back" aria-label="Card back">
  <p class="address">118 Ridgeline Way<br>Salem, OR 97301</p>
  <div class="title-band">
    <p class="title-band__name">DANIEL HART</p>
    <p class="title-band__role">Director</p>
  </div>
  <div class="emblem"></div>
  <p class="emblem-name">KEYSTONE<br>CHIROPRACTIC</p>
  <ul class="contact-list">
    <li>
      <svg viewBox="0 0 16 16" aria-hidden="true"><path d="M3.6 1.2l2.3 2.9-1.4 1.6c.9 2 2.6 3.7 4.6 4.6l1.6-1.4 2.9 2.3-1.3 2.4C7.1 13.6 2.4 8.9 1.2 3.1z"/></svg>
      (555) 214-0387
    </li>
    <li>
      <svg viewBox="0 0 16 16" aria-hidden="true"><path d="M1 3h14v10H1zm1.5 1.3v.3L8 8.6l5.5-4v-.3zM2.5 6.2v5.5h11V6.2L8 10.2z"/></svg>
      info@keystonechiro.com
    </li>
    <li>
      <svg viewBox="0 0 16 16" aria-hidden="true"><path d="M8 1a7 7 0 100 14A7 7 0 008 1zm-5.4 6.3h2.5c.1-1.6.5-3 1.1-4A5.6 5.6 0 002.6 7.3zm0 1.4a5.6 5.6 0 003.6 4c-.6-1-1-2.4-1.1-4zm4 0c.1 1.9.8 3.6 1.4 4.4.6-.8 1.3-2.5 1.4-4.4zm0-1.4h2.8C9.3 5.4 8.6 3.7 8 2.9c-.6.8-1.3 2.5-1.4 4.4zm4.3 1.4c-.1 1.6-.5 3-1.1 4a5.6 5.6 0 003.6-4zm2.5-1.4a5.6 5.6 0 00-3.6-4c.6 1 1 2.4 1.1 4z"/></svg>
      <span>www.<span class="accent">keystonechiro</span>.com</span>
    </li>
  </ul>
</section>

</body>
</html>
```